Brookvane Consulting Business Card Design

Business Card Design for Brookvane Consulting. Brookvane Consulting is a boutique consultancy based in Atlanta, GA., that specializes in marketing strategy, organization planning, and leadership development. We provide solutions for small businesses and startups as well as Vantage 300 companies.

http://brookvaneconsulting.com/

Target Market(s)

We provide solutions for small businesses and startups as well as Vantage 300 companies.

Industry/Entity Type

Consulting

Contact Information for Business Card

Two sided business card with priority on contact information, logo, tag line (Inspiration to Dream More, Do More, Become More)

Colors

Designer to choose colors to be used in the design.

Requirements
Must have
• contact information, logo, tag line (Inspiration to Dream More, Do More, Become More)
• Simple no over communication.
Nice to have
• I would like to see different placements of logo and creative use of both sides of the card
Should not have
• Do not put too much information on the card.

```html
<!DOCTYPE html>
<html lang="en">
<head>
<meta charset="utf-8">
<title>Brookvane Consulting – Business Card</title>
<link rel="stylesheet" href="https://fonts.googleapis.com/css2?family=Oswald:wght@500&family=Work+Sans:wght@400;500&display=swap">
<style>
  :root {
    --backdrop: #161616;
    --card: #1f1f1f;
    --card-edge: #2a2a2a;
    --ink: #f4f4f4;
    --ink-soft: #d9d9d9;
  }
  * { box-sizing: border-box; margin: 0; padding: 0; }
  html, body {
    width: 1200px; height: 900px; overflow: hidden;
    background: var(--backdrop);
    font-family: "Work Sans", sans-serif;
    color: var(--ink);
  }
  .sheet {
    width: 1200px; height: 900px;
    display: flex; flex-direction: column; align-items: center; justify-content: center;
    gap: 40px;
  }
  .card {
    position: relative;
    width: 630px; height: 360px;
    overflow: hidden;
    background: radial-gradient(circle at 75% 30%, #2a2a2a 0%, var(--card) 60%);
    border: 1px solid var(--card-edge);
  }
  /* Front side */
  .card-front {
    display: flex; flex-direction: column; align-items: center; justify-content: center;
  }
  .brand-name {
    font-size: 46px; font-weight: 500; letter-spacing: 1px;
    color: var(--ink);
  }
  .tagline {
    margin-top: 48px;
    font-size: 16px; letter-spacing: 1px;
    color: var(--ink-soft);
  }
  /* Back side */
  .identity {
    position: absolute; right: 356px; top: 132px;
    text-align: right;
  }
  .person-name {
    font-family: "Oswald", sans-serif; font-weight: 500;
    font-size: 36px; letter-spacing: 2px; text-transform: uppercase; line-height: 1.1;
  }
  .person-role { font-size: 16px; letter-spacing: 1px; color: var(--ink-soft); margin-top: 4px; }
  .divider {
    position: absolute; left: 292px; top: 140px;
    width: 2px; height: 76px; background: var(--ink);
  }
  .contact-list {
    position: absolute; left: 314px; top: 142px;
    list-style: none;
  }
  .contact-item {
    display: flex; align-items: center; gap: 10px;
    font-size: 14px; letter-spacing: 0.6px; line-height: 24px;
    white-space: nowrap;
  }
  .contact-icon { width: 14px; height: 14px; flex: none; fill: none; stroke: var(--ink); stroke-width: 1.6; }
  .contact-icon.solid { fill: var(--ink); stroke: none; }
  .address {
    position: absolute; left: 120px; bottom: 52px;
    font-size: 16px; letter-spacing: 1px;
  }
</style>
</head>
<body>
<main class="sheet">
  <section class="card card-front" aria-label="Card front">
    <div class="brand-name">Brookvane Consulting</div>
    <p class="tagline">Inspiration to Dream More, Do More, Become More</p>
  </section>

  <section class="card card-back" aria-label="Card back">
    <div class="identity">
      <h1 class="person-name">Daniel Reyes</h1>
      <p class="person-role">Managing Director</p>
    </div>
    <div class="divider"></div>
    <ul class="contact-list">
      <li class="contact-item">
        <svg class="contact-icon solid" viewBox="0 0 24 24"><path d="M6.6 10.8a15 15 0 0 0 6.6 6.6l2.2-2.2c.3-.3.7-.4 1-.2 1.1.4 2.3.6 3.6.6.6 0 1 .4 1 1V20c0 .6-.4 1-1 1A17 17 0 0 1 3 4c0-.6.4-1 1-1h3.5c.6 0 1 .4 1 1 0 1.3.2 2.5.6 3.6.1.3 0 .7-.2 1z"/></svg>
        <span>424-555-0192</span>
      </li>
      <li class="contact-item">
        <svg class="contact-icon" viewBox="0 0 24 24"><rect x="2" y="5" width="20" height="14"/><path d="M2 5l10 8 10-8"/></svg>
        <span>dreyes@brookvaneconsulting.com</span>
      </li>
      <li class="contact-item">
        <svg class="contact-icon" viewBox="0 0 24 24"><circle cx="12" cy="12" r="10"/><path d="M2 12h20M12 2c3 3 3 17 0 20M12 2c-3 3-3 17 0 20"/></svg>
        <span>www.brookvaneconsulting.com</span>
      </li>
    </ul>
    <p class="address">1024 Budapest, Lindenhof str. 18/B, Hungary</p>
  </section>
</main>
</body>
</html>
```